Fire Risk Assessment App needs a sleek UI design

I need a sleek, modern but professional design for my 5 page Fire Risk Assessment App. Include gradient background, fire themed colours including reds, yellows, light orange and a touch of black. Design must ooze simplicity and professionalism. This is for the UK market. See attached images and word doc for more information.

Target Market(s)

General public and business owners

Industry/Entity Type

Technology / Fire Safety

Colors
00AB8E
00BBA5
67D7C9
C6EFE9
E9F9F6
59FF00
82FF00
B8FF75
E3FFCB
F4FFEA
FFC000
F8CF3A
FAE287
FDF2CF
FEFAEE
F0912C
F2A743
F7CA91
FBE8D2
FDF5EE
EE7325
F08F49
F5BC92
FAE3D3
FDF4ED
EB3D1F
EC4F4E
F09395
F8D3D4
FCEDEE

```html
<!DOCTYPE html>
<html lang="en">
<head>
<meta charset="utf-8">
<title>Fire Risk Assessment App – UI Screens</title>
<link href="https://fonts.googleapis.com/css2?family=Outfit:wght@300;400;500;600&display=swap" rel="stylesheet">
<style>
:root{
  --canvas:#1f2236;
  --canvas-text:#272b41;
  --ink:#24242c;
  --muted:#55545a;
  --red:#eb3d1f;
  --orange:#ee7325;
  --orange-2:#f0912c;
  --amber:#ffc000;
  --cream:#fefaee;
  --sand:#fdf2cf;
  --nav:#f9e4a9;
  --green:#59ff00;
  --green-2:#82ff00;
  --teal:#00ab8e;
  --teal-2:#67d7c9;
  --row:rgba(255,255,255,.5);
}
*{box-sizing:border-box;margin:0;padding:0}
html,body{width:1200px;height:1200px;overflow:hidden;background:var(--canvas);font-family:"Outfit",sans-serif;color:var(--ink)}
.canvas{position:relative;width:1200px;height:1200px;overflow:hidden}
.backdrop-title{position:absolute;left:66px;top:960px;font-size:146px;font-weight:500;color:var(--canvas-text);white-space:nowrap;letter-spacing:1px;line-height:1}
.screen{position:absolute;width:232px;overflow:hidden;background:linear-gradient(180deg,#fefaec 0%,#fdf1cf 55%,#fbe5a9 100%)}
.abs{position:absolute}
.center{left:0;right:0;text-align:center}
.screen-title{font-size:15px;font-weight:400;color:var(--ink)}
.screen-sub{font-size:8px;color:var(--muted)}
.nav{position:absolute;left:0;right:0;bottom:0;height:41px;background:linear-gradient(180deg,#fbeab8,#f8e09e)}
.nav svg{position:absolute;top:14px;width:14px;height:14px;fill:var(--ink)}
.nav svg.active{fill:var(--orange)}
.nav-mark{position:absolute;top:0;width:26px;height:2px;border-radius:2px;background:var(--orange)}
.start-ring{width:142px;height:142px;border-radius:50%;border:14px solid rgba(240,224,178,.55);left:45px}
.start-button{width:78px;height:78px;border-radius:50%;left:77px;background:radial-gradient(circle at 40% 35%,#fbb324,#f28a1a 55%,#ec6418);box-shadow:0 6px 12px rgba(232,108,24,.35)}
.start-button::before,.start-button::after{content:"";position:absolute;background:#fff;border-radius:2px;left:50%;top:50%;transform:translate(-50%,-50%)}
.start-button::before{width:16px;height:3px}
.start-button::after{width:3px;height:16px}
.tab{font-size:8.5px;color:var(--muted)}
.tab.on{color:var(--orange)}
.section-label{left:10px;font-size:8.5px;color:var(--orange)}
.row{position:absolute;left:10px;width:212px;background:var(--row);border-radius:9px;font-size:8.5px;font-weight:500;padding-left:10px;display:flex;align-items:center;justify-content:space-between;padding-right:10px}
.row.light{font-weight:400}
.tick{width:12px;height:12px;border-radius:50%;background:var(--green-2);display:flex;align-items:center;justify-content:center}
.tick svg{width:8px;height:8px}
.progress{width:22px;height:22px;position:relative;color:var(--ink)}
.progress svg{position:absolute;left:0;top:0;width:100%;height:100%}
.progress span{position:absolute;inset:0;display:flex;align-items:center;justify-content:center;font-size:6px;font-weight:500;color:var(--ink)}
/* welcome */
.hero-title{font-size:15px;line-height:18px;font-weight:400}
.hero-title em{font-style:normal;color:var(--red);font-weight:500}
.pill{position:absolute;height:29px;border-radius:15px;display:flex;align-items:center;justify-content:center;font-size:8.5px;font-weight:500}
.pill .disc{position:absolute;left:3px;top:3px;width:23px;height:23px;border-radius:50%;display:flex;align-items:center;justify-content:center}
.pill .disc svg{width:11px;height:11px;fill:#fff}
.create-btn{left:42px;width:149px;background:linear-gradient(90deg,#67d7c9,#59ff00);color:var(--ink);box-shadow:0 4px 10px rgba(89,255,0,.25)}
.create-btn .disc{background:linear-gradient(135deg,#b8ff75,#82ff00)}
.create-btn .disc svg{fill:var(--ink)}
.login-btn{left:42px;width:149px;border:1px solid var(--red);background:transparent}
.login-btn .disc{background:linear-gradient(135deg,#f2a743,#ee7325)}
.mini-card{position:absolute;border-radius:9px;overflow:hidden}
.mini-front{left:54px;top:101px;width:126px;height:224px;background:linear-gradient(180deg,#ec4f24,#f08f2c 60%,#ffc000);box-shadow:0 8px 18px rgba(235,61,31,.3)}
.mini-back-red{left:30px;top:118px;width:100px;height:190px;background:linear-gradient(180deg,#ec4f4e,#eb3d1f);transform:rotate(-14deg)}
.mini-back-teal{left:110px;top:118px;width:100px;height:190px;background:linear-gradient(180deg,#00bba5,#00ab8e);transform:rotate(14deg)}
.mini-text{position:absolute;left:9px;color:#fff;font-size:5.6px;line-height:7px}
.mini-panel{position:absolute;left:7px;top:100px;width:112px;height:118px;background:#fdf3d6;border-radius:6px}
.mini-dot{position:absolute;top:48px;width:6px;height:6px;border-radius:50%}
.photo-chip{position:absolute;border-radius:50%;background:#fff;border:2px solid var(--green-2);display:flex;align-items:center;justify-content:center}
/* purchase */
.plan-panel{left:10px;top:68px;width:212px;height:370px;border-radius:12px;background:linear-gradient(200deg,#eb3d1f 0%,#f07a25 35%,#f59a2c 70%,#f8b334 100%);box-shadow:0 6px 16px rgba(235,61,31,.25)}
.plan-heading{font-size:9.5px;line-height:12px;color:#fff;font-weight:500}
.plan{position:absolute;left:10px;width:191px;height:62px;border-radius:7px;background:linear-gradient(180deg,rgba(255,255,255,.28),rgba(255,255,255,.12));color:#fff;text-align:center}
.plan .radio{position:absolute;left:9px;top:9px;width:14px;height:14px;border-radius:50%;border:1px solid rgba(255,255,255,.75)}
.plan .name{margin-top:13px;font-size:8.5px;font-weight:500;letter-spacing:.2px}
.plan .count{font-size:5.6px;margin-top:2px}
.plan .was{font-size:6px;text-decoration:line-through;margin-top:2px;opacity:.8}
.plan .price{font-size:8.5px;font-weight:600;margin-top:2px}
.checkout{left:10px;width:191px;top:328px;height:29px;border-radius:15px;background:linear-gradient(90deg,#eb3d1f,#f0912c);color:#fff}
.checkout .disc{background:linear-gradient(135deg,#f2a743,#ee7325)}
/* question */
.brief-card{left:10px;top:34px;width:211px;height:102px;border-radius:11px;background:linear-gradient(100deg,#ee6a22,#f08f2c 60%,#ec4f24);color:#fff}
.brief-line{position:absolute;left:16px;font-size:8px;line-height:12.5px}
.brief-line b{font-weight:600}
.question-card{left:10px;top:162px;width:211px;height:282px;border-radius:11px;background:rgba(255,255,255,.4)}
.bolt{left:97px;top:145px;width:35px;height:35px;border-radius:50%;background:radial-gradient(circle at 40% 35%,#fbb324,#ec6418);box-shadow:0 4px 10px rgba(232,108,24,.4);display:flex;align-items:center;justify-content:center}
.answer{position:absolute;top:235px;width:32px;height:31px;border-radius:5px;background:rgba(255,255,255,.6);display:flex;align-items:center;justify-content:center}
.answer.picked{border:1px solid var(--orange-2)}
.answer .dot{width:11px;height:11px;border-radius:50%;display:flex;align-items:center;justify-content:center}
.note-field{left:26px;top:276px;width:179px;height:20px;border-radius:5px;background:rgba(255,255,255,.6);font-size:7.5px;color:var(--muted);display:flex;align-items:center;justify-content:center}
.evidence{left:26px;top:306px;width:179px;height:82px;border-radius:4px;background:linear-gradient(135deg,#5c5c60,#d0d0d2 55%,#8a8a8e)}
.save-btn{left:26px;top:402px;width:85px;border:1px solid var(--orange-2);font-weight:400}
.save-btn .disc{background:linear-gradient(135deg,#f2a743,#ee7325)}
.next-btn{left:119px;top:402px;width:86px;background:linear-gradient(90deg,#67d7c9,#59ff00);font-weight:400}
.next-btn .disc{left:auto;right:3px;background:linear-gradient(135deg,#b8ff75,#82ff00)}
.next-btn .disc svg{fill:none;stroke:var(--ink)}
/* support */
.message-box{left:10px;top:76px;width:211px;height:127px;border-radius:9px;border:1px solid #f5dca0;background:rgba(255,255,255,.35);font-size:7.5px;color:var(--muted);padding:14px 15px}
.mic-btn{left:189px;top:172px;width:23px;height:23px;border-radius:50%;background:radial-gradient(circle at 40% 35%,#f7a21b,#ee6a18);display:flex;align-items:center;justify-content:center;box-shadow:0 3px 7px rgba(232,108,24,.35)}
.send-btn{left:10px;top:211px;width:211px;background:linear-gradient(90deg,#eb3d1f,#f0912c);color:#fff;font-weight:400}
.send-btn .disc{background:linear-gradient(135deg,#f2a743,#ee7325)}
.footnote{font-size:8px;color:var(--muted)}
</style>
</head>
<body>
<svg width="0" height="0" style="position:absolute">
  <defs>
    <symbol id="i-gauge" viewBox="0 0 24 24"><path d="M12 2a10 10 0 1 0 0 20 10 10 0 0 0 0-20zm0 3a7 7 0 1 1 0 14 7 7 0 0 1 0-14z"/><path d="M11 13l5-6 1.2 1-4.8 6.4z"/></symbol>
    <symbol id="i-card" viewBox="0 0 24 24"><path d="M4 5h16a2 2 0 0 1 2 2v10a2 2 0 0 1-2 2H4a2 2 0 0 1-2-2V7a2 2 0 0 1 2-2zm-2 4v3h20V9z"/><rect x="5" y="14" width="5" height="1.6" fill="#fff"/></symbol>
    <symbol id="i-chat" viewBox="0 0 24 24"><path d="M5 3h14a3 3 0 0 1 3 3v8a3 3 0 0 1-3 3h-8l-5 4v-4a3 3 0 0 1-3-3V6a3 3 0 0 1 3-3z"/><rect x="8" y="9" width="8" height="2" fill="#fff"/></symbol>
    <symbol id="i-user" viewBox="0 0 24 24"><circle cx="9" cy="7" r="4.5"/><path d="M1 22c0-5 3.5-8 8-8 2 0 3.6.5 5 1.5V22z"/><path d="M15 18h6m-2.5-3l3 3-3 3" fill="none" stroke="currentColor" stroke-width="2"/></symbol>
    <symbol id="i-check" viewBox="0 0 24 24"><path d="M5 12.5l4.5 4.5L19 7.5" fill="none" stroke="#fff" stroke-width="3.5" stroke-linecap="round" stroke-linejoin="round"/></symbol>
    <symbol id="i-image" viewBox="0 0 24 24"><rect x="3" y="4" width="18" height="16" rx="2.5" fill="none" stroke="#c9c2b0" stroke-width="2"/><circle cx="9" cy="9.5" r="1.8" fill="#c9c2b0"/><path d="M4 18l5-5 3.5 3.5L16 13l4 4v1H4z" fill="#c9c2b0"/></symbol>
  </defs>
</svg>

<div class="canvas">
  <div class="backdrop-title">Fire Assessment</div>

  <!-- Welcome -->
  <section class="screen" style="left:104px;top:51px;height:502px">
    <div class="abs center hero-title" style="top:33px">The Most <em>User Friendly</em><br>Fire Risk Assessment App<br>Available</div>
    <div class="mini-card mini-back-red"></div>
    <div class="mini-card mini-back-teal"></div>
    <div class="mini-card mini-front">
      <div class="mini-text" style="top:9px">Fire Risk Assessment<br>Fire Hazards<br>Section: 7.00/30.00</div>
      <div class="progress" style="position:absolute;left:98px;top:9px;width:17px;height:17px"><svg viewBox="0 0 22 22"><circle cx="11" cy="11" r="10" fill="#fff"/><circle cx="11" cy="11" r="10" fill="none" stroke="#82ff00" stroke-width="1.8" stroke-dasharray="19 63" transform="rotate(-90 11 11)"/></svg><span style="font-size:4.6px">30%</span></div>
      <div class="mini-text" style="top:54px;font-weight:600">ELECTRONIC SOURCES<br>OF IGNITION</div>
      <div class="mini-text" style="top:69px">(Clause 13 &amp; Annex B)</div>
      <span class="photo-chip" style="left:98px;top:54px;width:17px;height:17px"><svg width="8" height="8"><use href="#i-image"/></svg></span>
      <div class="mini-panel">
        <div class="abs" style="left:8px;top:14px;font-size:5.4px;line-height:7px">Q: 7.01<br><br>Are resonable measures taken to<br>prevent fires of electrical origin?</div>
        <span class="mini-dot" style="left:10px;background:var(--teal)"></span>
        <span class="mini-dot" style="left:32px;background:var(--red)"></span>
        <span class="mini-dot" style="left:54px;background:var(--orange-2)"></span>
        <span class="mini-dot" style="left:76px;background:var(--amber)"></span>
        <span class="mini-dot" style="left:98px;background:#ec4f4e"></span>
        <div class="abs" style="left:6px;top:60px;width:100px;height:10px;border-radius:3px;background:rgba(255,255,255,.7);font-size:4.6px;text-align:center;line-height:10px;color:var(--muted)">No, electric sockets are overloaded</div>
        <div class="abs" style="left:6px;top:76px;width:100px;height:34px;border-radius:3px;background:#f7e8b8;display:flex;align-items:center;justify-content:center"><svg width="11" height="11"><use href="#i-image"/></svg></div>
      </div>
    </div>
    <div class="abs center footnote" style="top:341px">Quick tap response and voice activated typing</div>
    <div class="pill create-btn" style="top:361px"><span class="disc"><svg viewBox="0 0 24 24"><use href="#i-user"/></svg></span>Create a Free Account</div>
    <div class="abs center footnote" style="top:408px">Any <span style="color:var(--red)">responsible person</span> can do it.</div>
    <div class="pill login-btn" style="top:429px"><span class="disc"><svg viewBox="0 0 24 24"><use href="#i-user"/></svg></span>Customer Login</div>
    <div class="abs center footnote" style="top:471px;font-size:7.5px">Created and endorsed by Hearth Safety Guild</div>
  </section>

  <!-- Dashboard: completed -->
  <section class="screen" style="left:361px;top:51px;height:512px">
    <div class="abs center screen-title" style="top:33px">Dashboard</div>
    <div class="abs center screen-sub" style="top:54px">Start Fire Assessment</div>
    <div class="abs start-ring" style="top:73px"></div>
    <div class="abs start-button" style="top:105px"></div>
    <div class="abs tab on" style="left:60px;top:207px">Completed</div>
    <div class="abs tab" style="left:129px;top:207px">In Progress</div>
    <div class="row" style="top:232px;height:32px">Reno’s Barbershop<span class="tick"><svg><use href="#i-check"/></svg></span></div>
    <div class="row" style="top:271px;height:33px">The Kettle Café<span class="tick"><svg><use href="#i-check"/></svg></span></div>
    <div class="abs section-label" style="top:321px">Purchases</div>
    <div class="row" style="top:347px;height:32px">Residential Fire Risk Assessment</div>
    <div class="row" style="top:387px;height:32px">Commercial Fire Risk Assessment</div>
    <nav class="nav">
      <span class="nav-mark" style="left:18px"></span>
      <svg class="active" style="left:24px"><use href="#i-gauge"/></svg>
      <svg style="left:80px"><use href="#i-card"/></svg>
      <svg style="left:137px"><use href="#i-chat"/></svg>
      <svg style="left:193px;color:var(--ink)"><use href="#i-user"/></svg>
    </nav>
  </section>

  <!-- Dashboard: in progress -->
  <section class="screen" style="left:618px;top:51px;height:512px">
    <div class="abs center screen-title" style="top:33px">Dashboard</div>
    <div class="abs center screen-sub" style="top:54px">Start Fire Assessment</div>
    <div class="abs start-ring" style="top:73px"></div>
    <div class="abs start-button" style="top:105px"></div>
    <div class="abs tab" style="left:60px;top:207px">Completed</div>
    <div class="abs tab on" style="left:128px;top:207px">In Progress</div>
    <div class="row" style="top:232px;height:40px">Alder Road School
      <span class="progress"><svg viewBox="0 0 22 22"><circle cx="11" cy="11" r="10" fill="#fff"/><circle cx="11" cy="11" r="10" fill="none" stroke="#82ff00" stroke-width="1.8" stroke-dasharray="19 63" transform="rotate(-90 11 11)"/></svg><span>30%</span></span></div>
    <div class="row" style="top:280px;height:40px">Willow Court Nursing Home
      <span class="progress"><svg viewBox="0 0 22 22"><circle cx="11" cy="11" r="10" fill="#fff"/><circle cx="11" cy="11" r="10" fill="none" stroke="#82ff00" stroke-width="1.8" stroke-dasharray="25 63" transform="rotate(-90 11 11)"/></svg><span>40%</span></span></div>
    <div class="abs section-label" style="top:336px">Purchases</div>
    <div class="row" style="top:361px;height:32px">Residential Fire Risk Assessment</div>
    <div class="row light" style="top:401px;height:32px">Commercial Fire Risk Assessment</div>
    <nav class="nav">
      <span class="nav-mark" style="left:18px"></span>
      <svg class="active" style="left:24px"><use href="#i-gauge"/></svg>
      <svg style="left:80px"><use href="#i-card"/></svg>
      <svg style="left:137px"><use href="#i-chat"/></svg>
      <svg style="left:193px;color:var(--ink)"><use href="#i-user"/></svg>
    </nav>
  </section>

  <!-- Purchase options -->
  <section class="screen" style="left:874px;top:51px;height:502px">
    <div class="abs center screen-title" style="top:33px">Purchase Options</div>
    <div class="abs plan-panel">
      <div class="abs center plan-heading" style="top:14px">FIRE RISK ASSESSMENT<br>PURCHASE OPTIONS</div>
      <div class="plan" style="top:53px"><span class="radio"></span><div class="name">BRONZE</div><div class="count">1 Fire Risk Assessment</div><div class="price">£19.99</div></div>
      <div class="plan" style="top:119px"><span class="radio"></span><div class="name" style="margin-top:8px">SILVER</div><div class="count">3 Fire Risk Assessments</div><div class="was">£59.97</div><div class="price">£54.99</div></div>
      <div class="plan" style="top:188px"><span class="radio"></span><div class="name" style="margin-top:8px">GOLD</div><div class="count">5 Fire Risk Assessments</div><div class="was">£99.95</div><div class="price">£89.99</div></div>
      <div class="plan" style="top:256px"><span class="radio"></span><div class="name" style="margin-top:8px">PLATINUM</div><div class="count">10 Fire Risk Assessments</div><div class="was">£199.90</div><div class="price">£174.99</div></div>
      <div class="pill checkout abs"><span class="disc"><svg viewBox="0 0 24 24"><path d="M6 8h12l1 13H5zm3 0V6a3 3 0 0 1 6 0v2h-2V6a1 1 0 0 0-2 0v2z"/></svg></span>Checkout</div>
    </div>
    <nav class="nav">
      <span class="nav-mark" style="left:74px"></span>
      <svg style="left:24px"><use href="#i-gauge"/></svg>
      <svg class="active" style="left:80px"><use href="#i-card"/></svg>
      <svg style="left:137px"><use href="#i-chat"/></svg>
      <svg style="left:193px;color:var(--ink)"><use href="#i-user"/></svg>
    </nav>
  </section>

  <!-- Assessment question -->
  <section class="screen" style="left:356px;top:593px;height:501px">
    <div class="abs brief-card">
      <div class="brief-line" style="top:12px">Fire Risk Assessment<br>Fire Hazards<br>Section: 7.00/30.00</div>
      <div class="brief-line" style="top:65px;line-height:11px"><b>ELECTRONIC SOURCES OF IGNITION</b><br>(Clause 13 &amp; Annex B)</div>
      <div class="progress" style="position:absolute;left:168px;top:12px;width:26px;height:26px"><svg viewBox="0 0 22 22"><circle cx="11" cy="11" r="10" fill="#fff"/><circle cx="11" cy="11" r="10" fill="none" stroke="#82ff00" stroke-width="1.8" stroke-dasharray="19 63" transform="rotate(-90 11 11)"/></svg><span style="font-size:7px">30%</span></div>
      <span class="photo-chip" style="left:170px;top:64px;width:24px;height:24px"><svg width="11" height="11"><use href="#i-image"/></svg></span>
    </div>
    <div class="abs question-card"></div>
    <div class="abs bolt"><svg width="14" height="16" viewBox="0 0 14 16"><path d="M8 0L1 9h5l-1 7 7-9H7z" fill="#2a2320"/></svg></div>
    <div class="abs" style="left:26px;top:187px;font-size:7.5px">Q: 7.01</div>
    <div class="abs" style="left:26px;top:200px;font-size:9.5px;line-height:12px">Are resonable measures taken to<br>prevent fires of electrical origin?</div>
    <div class="answer" style="left:26px"><span class="dot" style="background:var(--teal)"><svg width="7" height="7"><use href="#i-check"/></svg></span></div>
    <div class="answer" style="left:63px"><span class="dot" style="background:var(--red);color:#fff;font-size:7px">×</span></div>
    <div class="answer picked" style="left:100px"><span class="dot" style="background:var(--orange-2)"><span style="width:5px;height:1.5px;background:#fff"></span></span></div>
    <div class="answer" style="left:137px"><svg width="13" height="12" viewBox="0 0 13 12"><rect x="0.8" y="2.5" width="11.4" height="8.7" rx="1.5" fill="none" stroke="#ffc000" stroke-width="1.4"/><circle cx="6.5" cy="6.8" r="2.3" fill="none" stroke="#ffc000" stroke-width="1.4"/><rect x="4" y="0.6" width="5" height="2" fill="#ffc000"/></svg></div>
    <div class="answer" style="left:174px"><svg width="9" height="13" viewBox="0 0 9 13"><rect x="2.5" y="0.5" width="4" height="7.5" rx="2" fill="#eb3d1f"/><path d="M1 6a3.5 3.5 0 0 0 7 0M4.5 9.5V12" fill="none" stroke="#eb3d1f" stroke-width="1.2"/></svg></div>
    <div class="abs note-field">No, electric sockets are overloaded</div>
    <div class="abs evidence" role="img" aria-label="Photo evidence of a burning electrical cabinet"></div>
    <div class="pill save-btn"><span class="disc"><svg viewBox="0 0 24 24"><path d="M9 6L4 10l5 4v-3h6a3 3 0 0 1 0 6h-4v2h4a5 5 0 0 0 0-10H9z"/></svg></span><span style="margin-left:22px">Save &amp; Exit</span></div>
    <div class="pill next-btn"><span style="margin-right:22px">Next</span><span class="disc"><svg viewBox="0 0 24 24"><path d="M4 12h15m-5-5l5 5-5 5" stroke-width="2.4"/></svg></span></div>
    <nav class="nav">
      <svg style="left:24px"><use href="#i-gauge"/></svg>
      <svg style="left:80px"><use href="#i-card"/></svg>
      <svg style="left:137px"><use href="#i-chat"/></svg>
      <svg style="left:193px;color:var(--ink)"><use href="#i-user"/></svg>
    </nav>
  </section>

  <!-- Technical support -->
  <section class="screen" style="left:612px;top:593px;height:501px">
    <div class="abs center screen-title" style="top:33px">Technical Support</div>
    <div class="abs center screen-sub" style="top:54px">Type/Record Your Response Here</div>
    <div class="abs message-box">Write your message here...</div>
    <div class="abs mic-btn"><svg width="9" height="13" viewBox="0 0 9 13"><rect x="2.5" y="0.5" width="4" height="7.5" rx="2" fill="#fff"/><path d="M1 6a3.5 3.5 0 0 0 7 0M4.5 9.5V12" fill="none" stroke="#fff" stroke-width="1.2"/></svg></div>
    <div class="pill send-btn"><span class="disc"><svg viewBox="0 0 24 24"><path d="M21 3L3 11l7 2 2 7z"/></svg></span>Send</div>
    <nav class="nav">
      <span class="nav-mark" style="left:131px"></span>
      <svg style="left:24px"><use href="#i-gauge"/></svg>
      <svg style="left:80px"><use href="#i-card"/></svg>
      <svg class="active" style="left:137px"><use href="#i-chat"/></svg>
      <svg style="left:193px;color:var(--ink)"><use href="#i-user"/></svg>
    </nav>
  </section>
</div>
</body>
</html>
```